business card deign

Logo needs the following on it.
1. attached logo
2. Tagline - "From chilled coolers to lively gatherings...we bring it!"
3. Name- Dalton Pikes, Founder and CPO
4. Address - 412 E. Carver Avenue, Ste 2207, Tampa, FL. 33917
5. Phone - 555.318.4726

```html
<!DOCTYPE html>
<html lang="en">
<head>
<meta charset="utf-8">
<title>Hopwell Business Card</title>
<link href="https://fonts.googleapis.com/css2?family=Montserrat:wght@400;600;800&display=swap" rel="stylesheet">
<style>
  :root {
    --stage: #2a2a2e;
    --ink: #111111;
    --card-dark: #0d0d0d;
    --paper: #ffffff;
    --silver: #9a9a9a;
    --muted: #3a3a3a;
  }
  * { box-sizing: border-box; margin: 0; padding: 0; }
  html, body {
    width: 1200px; height: 864px; overflow: hidden;
    background: var(--stage);
    font-family: "Montserrat", Arial, sans-serif;
  }
  .canvas {
    width: 1200px; height: 864px;
    display: flex; align-items: center; justify-content: center; gap: 40px;
  }
  .card {
    position: relative;
    width: 540px; height: 320px;
    border-radius: 22px;
    overflow: hidden;
    box-shadow: 0 18px 40px rgba(0,0,0,.45);
  }

  /* Front: dark side */
  .card-front { background: var(--card-dark); }
  .front-pattern {
    position: absolute; inset: 0;
    background: linear-gradient(115deg, #d9d9d9 0%, #7a7a7a 22%, #2a2a2a 48%, #141414 75%, #0b0b0b 100%);
    opacity: .55;
  }
  .front-brand {
    position: absolute; inset: 0;
    display: flex; align-items: center; justify-content: center; gap: 14px;
  }
  .brand-dot {
    flex: none;
    width: 18px; height: 18px; border-radius: 50%;
    background: var(--paper);
  }
  .brand-name {
    font-weight: 800; font-size: 40px; letter-spacing: 10px;
    color: var(--paper); white-space: nowrap;
  }

  /* Back: contact side */
  .card-back { background: var(--paper); }
  .back-logo {
    position: absolute; left: 34px; top: 96px;
    display: flex; align-items: center; gap: 10px;
  }
  .back-logo .brand-dot { background: var(--ink); width: 12px; height: 12px; }
  .back-logo .brand-name { color: var(--ink); font-size: 24px; letter-spacing: 4px; }
  .divider {
    position: absolute; left: 252px; top: 58px;
    width: 1.5px; height: 118px; background: var(--ink);
  }
  .contact {
    position: absolute; left: 272px; top: 46px;
    color: var(--ink);
  }
  .contact-name { font-weight: 800; font-size: 18px; letter-spacing: .5px; }
  .contact-title { font-size: 13px; margin-top: 2px; color: var(--muted); }
  .contact-row {
    display: flex; align-items: flex-start; gap: 8px;
    font-size: 13px; margin-top: 10px; line-height: 1.35;
  }
  .contact-row + .contact-row { margin-top: 4px; }
  .contact-row svg { flex: none; margin-top: 2px; }
  .wave { position: absolute; left: 0; bottom: 0; }
  .tagline {
    position: absolute; right: 26px; bottom: 16px;
    color: var(--paper);
    font-size: 12px; letter-spacing: .2px; white-space: nowrap;
  }
</style>
</head>
<body>
<main class="canvas">

  <section class="card card-front">
    <div class="front-pattern" role="img" aria-label="Repeating brand symbol pattern in silver fading to black"></div>
    <div class="front-brand">
      <span class="brand-dot"></span>
      <span class="brand-name">HOPWELL</span>
    </div>
  </section>

  <section class="card card-back">
    <div class="back-logo">
      <span class="brand-dot"></span>
      <span class="brand-name">HOPWELL</span>
    </div>
    <div class="divider"></div>
    <div class="contact">
      <p class="contact-name">DALTON PIKES</p>
      <p class="contact-title">Founder and CPO</p>
      <p class="contact-row">
        <svg width="12" height="12" viewBox="0 0 24 24" aria-hidden="true"><path fill="#111" d="M6.6 10.8a15 15 0 0 0 6.6 6.6l2.2-2.2a1 1 0 0 1 1-.25 11.4 11.4 0 0 0 3.6.57 1 1 0 0 1 1 1V20a1 1 0 0 1-1 1A17 17 0 0 1 3 4a1 1 0 0 1 1-1h3.5a1 1 0 0 1 1 1c0 1.25.2 2.45.57 3.57a1 1 0 0 1-.25 1z"/></svg>
        <span>555.318.4726</span>
      </p>
      <p class="contact-row">
        <svg width="12" height="14" viewBox="0 0 24 28" aria-hidden="true"><path fill="#111" d="M12 0a9 9 0 0 0-9 9c0 7 9 19 9 19s9-12 9-19a9 9 0 0 0-9-9zm0 13a4 4 0 1 1 0-8 4 4 0 0 1 0 8z"/></svg>
        <span>412 E. Carver Avenue, Ste<br>2207, Tampa, FL. 33917</span>
      </p>
    </div>
    <svg class="wave" width="540" height="130" viewBox="0 0 540 130" aria-hidden="true">
      <path d="M0 100 C 110 100, 150 40, 300 30 C 400 24, 470 14, 540 6 L540 18 C 470 28, 410 36, 310 44 C 170 56, 130 112, 0 112 Z" fill="var(--silver)"/>
      <path d="M0 116 C 120 116, 160 64, 310 54 C 410 47, 475 38, 540 30 L540 130 L0 130 Z" fill="var(--card-dark)"/>
    </svg>
    <p class="tagline">From chilled coolers to lively gatherings...we bring it!</p>
  </section>

</main>
</body>
</html>
```